wealth management firm, professional group, new model

we have a logo that works but we need a card, white background using our colors...clean look

our tag line if can be used in

The Bridge From Client to Owner

```html
<!DOCTYPE html>
<html lang="en">
<head>
<meta charset="utf-8">
<title>Arcwell Wealth Partners – Business Card</title>
<link href="https://fonts.googleapis.com/css2?family=Montserrat:wght@400;500;600;700&display=swap" rel="stylesheet">
<style>
  :root {
    --stage: #2e2e30;
    --navy: #172e52;
    --navy-raised: #24416f;
    --ink: #1b2a5c;
    --text: #1a1a1a;
    --paper: #ffffff;
  }
  * { box-sizing: border-box; margin: 0; padding: 0; }
  html, body { width: 1200px; height: 875px; overflow: hidden; }
  body {
    background: var(--stage);
    font-family: "Montserrat", sans-serif;
    position: relative;
  }
  .card {
    position: absolute;
    top: 283px;
    width: 540px;
    height: 309px;
    border-radius: 18px;
    overflow: hidden;
  }
  .card--front { left: 45px; background: var(--navy); }
  .card--back { left: 615px; background: var(--paper); }

  .brand-name {
    font-weight: 600;
    line-height: 1;
    white-space: nowrap;
  }

  .card--front .brand {
    position: absolute; left: 0; right: 0; top: 118px; text-align: center;
    color: var(--navy-raised);
  }
  .card--front .brand-name { font-size: 32px; }
  .tagline {
    margin-top: 14px;
    font-size: 14px;
    font-weight: 400;
    letter-spacing: 1px;
  }

  .card--back .brand {
    position: absolute; right: 30px; top: 40px;
    display: flex; align-items: center; gap: 10px;
    color: var(--ink);
  }
  .brand-square { width: 12px; height: 12px; background: var(--ink); }
  .card--back .brand-name { font-size: 22px; }

  .holder__tab {
    position: absolute; left: 0; top: 200px; width: 18px; height: 30px;
    background: var(--ink); border-radius: 0 5px 5px 0;
  }
  .holder {
    position: absolute; left: 34px; top: 194px; color: var(--ink);
  }
  .holder__name { font-size: 23px; font-weight: 700; text-transform: uppercase; line-height: 1; }
  .holder__role { font-size: 11px; color: var(--text); margin-top: 4px; }

  .contact {
    position: absolute; left: 52px; top: 242px; list-style: none;
    font-size: 11px; color: var(--text); line-height: 15px;
  }
  .contact li { display: flex; align-items: center; gap: 7px; }
  .contact svg { width: 9px; height: 9px; fill: var(--ink); }

  .divider {
    position: absolute; left: 268px; top: 222px; width: 1px; height: 28px; background: var(--ink);
  }
  .address {
    position: absolute; left: 282px; top: 221px; font-size: 11px; line-height: 15px; color: var(--text);
  }
</style>
</head>
<body>
  <section class="card card--front" aria-label="Card front">
    <div class="brand">
      <p class="brand-name">Arcwell Wealth Partners</p>
      <p class="tagline">The Bridge From Client to Owner</p>
    </div>
  </section>

  <section class="card card--back" aria-label="Card back">
    <div class="brand">
      <span class="brand-square"></span>
      <p class="brand-name">Arcwell Wealth Partners</p>
    </div>

    <span class="holder__tab"></span>
    <div class="holder">
      <p class="holder__name">Jordan Hale</p>
      <p class="holder__role">Manager</p>
    </div>

    <ul class="contact">
      <li><svg viewBox="0 0 10 10"><path d="M2 0.5 L3.8 2.6 L2.9 3.6 Q4 5.9 6.4 7.1 L7.4 6.2 L9.5 8 L8.2 9.5 Q1 8 0.5 1.8 Z"/></svg>+012 345 6789</li>
      <li><svg viewBox="0 0 10 10"><path d="M0 2 H10 V8 H0 Z M0.6 2.4 L5 5.6 L9.4 2.4 V2.6 L5 6.3 L0.6 2.6 Z" fill-rule="evenodd"/></svg>info@youremail.com</li>
      <li><svg viewBox="0 0 10 10"><circle cx="5" cy="5" r="4.5"/></svg>www.yourwebsite.com</li>
    </ul>

    <span class="divider"></span>
    <p class="address">Your loaction street here,<br>Your country name - 9120</p>
  </section>
</body>
</html>
```